business card deign

Logo needs the following on it.
1. attached logo
2. Tagline - "If it keeps a drink cold or the party going...we do it!"
3. Name- Dalton Pikes, Founder and CPO
4. Address - 412 E. Carver Avenue, Ste 2207, Tampa, FL. 33917
5. Phone - 555.318.4726

```html
<!DOCTYPE html>
<html lang="en">
<head>
<meta charset="utf-8">
<title>Tallora — Business Card</title>
<link href="https://fonts.googleapis.com/css2?family=Oswald:wght@600&family=Open+Sans:wght@400&family=Roboto:wght@400;900&display=swap" rel="stylesheet">
<style>
  :root {
    --stage: #232323;
    --card-black: #141414;
    --card-charcoal: #1d1d1d;
    --pattern-grey: #2c2c2c;
    --ink-white: #ffffff;
    --ink-black: #111111;
    --soft-grey: #9a9a9a;
  }
  * { margin: 0; padding: 0; box-sizing: border-box; }
  html, body {
    width: 1200px; height: 780px; overflow: hidden;
    background: var(--stage);
  }
  .stage {
    width: 1200px; height: 780px;
    display: flex; align-items: center; justify-content: center; gap: 40px;
  }
  .card {
    position: relative;
    width: 540px; height: 310px;
    border-radius: 22px;
    overflow: hidden;
    box-shadow: 0 18px 40px rgba(0,0,0,.55);
  }

  /* Front */
  .card--front { background: var(--card-black); }
  .front-pattern { position: absolute; inset: 0; width: 100%; height: 100%; }
  .front-brand {
    position: absolute; inset: 0;
    display: flex; flex-direction: column; align-items: center; justify-content: center; gap: 18px;
  }
  .brand-dot {
    width: 26px; height: 26px; border-radius: 50%;
    background: var(--ink-white);
  }
  .wordmark {
    font-family: "Oswald", sans-serif;
    font-weight: 600;
    color: var(--ink-white);
    letter-spacing: .42em;
    line-height: 1;
  }
  .front-brand .wordmark { font-size: 44px; padding-left: .42em; }

  /* Back */
  .card--back { background: var(--card-black); }
  .back-art { position: absolute; top: 0; left: 270px; width: 270px; height: 310px; }
  .back-info {
    position: absolute; left: 34px; top: 40px; width: 260px;
    color: var(--ink-white);
    font-family: "Open Sans", sans-serif;
  }
  .back-info .wordmark { font-size: 40px; }
  .tagline { margin-top: 40px; font-size: 14px; line-height: 1.35; }
  .contact { list-style: none; margin-top: 22px; font-size: 14px; line-height: 1.35; }
  .contact li { display: flex; gap: 8px; align-items: flex-start; margin-bottom: 2px; }
  .contact svg { flex: none; margin-top: 3px; }
  .person {
    position: absolute; right: 22px; top: 26px;
    writing-mode: vertical-rl;
    color: var(--ink-black);
    font-family: "Roboto", sans-serif;
    display: flex; gap: 4px;
  }
  .person-name { font-weight: 900; font-size: 30px; line-height: 1; }
  .person-role { font-weight: 400; font-size: 15px; line-height: 1; }
</style>
</head>
<body>
<main class="stage">

  <section class="card card--front" aria-label="Card front">
    <svg class="front-pattern" viewBox="0 0 540 310" role="img" aria-label="Repeating pattern of small brand marks in glossy black">
      <defs>
        <linearGradient id="frontSheen" x1="0" y1="1" x2="1" y2="0">
          <stop offset="0" stop-color="#141414"/>
          <stop offset=".6" stop-color="#1f1f1f"/>
          <stop offset="1" stop-color="#3a3a3a"/>
        </linearGradient>
      </defs>
      <rect width="540" height="310" fill="url(#frontSheen)"/>
    </svg>
    <div class="front-brand">
      <span class="brand-dot"></span>
      <span class="wordmark">TALLORA</span>
    </div>
  </section>

  <section class="card card--back" aria-label="Card back">
    <svg class="back-art" viewBox="0 0 270 310" role="img" aria-label="Large brand mascot silhouette in black outlined in white on a white field">
      <defs>
        <linearGradient id="mascotField" x1="0" y1="0" x2="1" y2="0">
          <stop offset="0" stop-color="#141414"/>
          <stop offset=".55" stop-color="#1a1a1a"/>
          <stop offset="1" stop-color="#ffffff"/>
        </linearGradient>
      </defs>
      <rect width="270" height="310" fill="url(#mascotField)"/>
      <rect x="165" width="105" height="310" fill="#ffffff"/>
    </svg>

    <div class="back-info">
      <div class="wordmark">TALLORA</div>
      <p class="tagline">If it keeps a drink cold or<br>the party going...we do it!</p>
      <ul class="contact">
        <li>
          <svg width="12" height="12" viewBox="0 0 24 24" aria-hidden="true"><path fill="#fff" d="M6.6 10.8a15.1 15.1 0 0 0 6.6 6.6l2.2-2.2c.3-.3.7-.4 1-.2 1.1.4 2.3.6 3.6.6.6 0 1 .4 1 1V20c0 .6-.4 1-1 1A17 17 0 0 1 3 4c0-.6.4-1 1-1h3.5c.6 0 1 .4 1 1 0 1.3.2 2.5.6 3.6.1.3 0 .7-.2 1z"/></svg>
          <span>555.318.4726</span>
        </li>
        <li>
          <svg width="12" height="14" viewBox="0 0 24 28" aria-hidden="true"><path fill="none" stroke="#fff" stroke-width="2.4" d="M12 26s8-8.5 8-14a8 8 0 0 0-16 0c0 5.5 8 14 8 14z"/><circle cx="12" cy="12" r="3" fill="#fff"/></svg>
          <span>412 E. Carver Avenue,<br>Ste 2207, Tampa, FL. 33917</span>
        </li>
      </ul>
    </div>

    <div class="person">
      <span class="person-name">Dalton Pikes</span>
      <span class="person-role">Founder and CPO</span>
    </div>
  </section>

</main>
</body>
</html>
```